Irrigation Business needs their business cards modernised and revamped

I would like to keep my current logo, colours and revamp the format of the card.

I would like the card to be clean yet important.

Im not sure if you include texture but i would like the named logo to be indented into the card etc.

show me something alive and free something thats clinical to the point yet has a feel of achievement. i would like people to go nice card.

Target Market(s)

high end clients, corporate, sports field manger, the guys that make the decisions

Industry/Entity Type

Business

Contact Information for Business Card

nformation to be included

Dean Harlow (Director)
0487305526
dean@kolvat.biz
www.kestonfieldworks.com

instagram logo
google logo
facebook logo

Colors

Designer to choose colors to be used in the design.

Requirements
Nice to have
• indentations a really nice feel to the card good texture

```html
<!DOCTYPE html>
<html lang="en">
<head>
<meta charset="utf-8">
<title>Keston Fieldworks – Business Card</title>
<link href="https://fonts.googleapis.com/css2?family=Oswald:wght@500&family=Roboto:wght@400;500;900&display=swap" rel="stylesheet">
<style>
  :root {
    --backdrop: #d7dadb;
    --card: #eef0ef;
    --card-edge: #c9cdcd;
    --navy: #1d3a78;
    --band-blue: #1f3f93;
    --band-green: #2f7d45;
    --green: #2f7a3c;
    --mark: #2d6f86;
    --ink: #2a2d30;
  }
  * { margin: 0; padding: 0; box-sizing: border-box; }
  html, body {
    width: 1200px; height: 969px; overflow: hidden;
    background: var(--backdrop);
  }
  .canvas {
    position: relative; width: 1200px; height: 969px;
  }
  .business-card {
    position: absolute; left: 365px; top: 75px;
    width: 470px; height: 820px;
    background: var(--card);
    border: 1px solid var(--card-edge);
    border-radius: 26px;
    overflow: hidden;
    box-shadow: 0 18px 40px rgba(0,0,0,0.12);
  }
  .brand-band {
    position: absolute; left: 0; top: 82px;
    width: 100%; height: 156px;
    background: linear-gradient(90deg, var(--band-blue) 0%, var(--band-blue) 38%, var(--band-green) 62%, var(--band-green) 100%);
  }
  .brand-dot {
    position: absolute; left: 50%; top: 78px;
    width: 120px; height: 120px; margin-left: -60px;
    border-radius: 50%;
    background: var(--mark);
  }
  .company-name {
    position: absolute; left: 0; top: 250px; width: 100%;
    text-align: center;
    font-family: "Roboto", sans-serif; font-weight: 900;
    font-size: 40px; letter-spacing: 0.5px;
    color: var(--navy);
  }
  .person {
    position: absolute; left: 0; top: 0; width: 100%; text-align: center;
  }
  .person-name {
    position: absolute; left: 0; top: 525px; width: 100%; text-align: center;
    font-family: "Oswald", sans-serif; font-weight: 500;
    font-size: 44px; letter-spacing: 1px;
    color: var(--navy);
  }
  .person-title {
    position: absolute; left: 0; top: 594px; width: 100%; text-align: center;
    font-family: "Roboto", sans-serif; font-weight: 500;
    font-size: 22px; letter-spacing: 1.5px;
    color: var(--green);
  }
  .divider {
    position: absolute; left: 50%; top: 640px;
    width: 32px; height: 2px; margin-left: -16px;
    background: var(--navy);
  }
  .contact-list {
    position: absolute; left: 0; top: 660px; width: 100%;
    list-style: none; text-align: center;
    font-family: "Roboto", sans-serif; font-weight: 400;
    font-size: 21px; line-height: 29px;
    color: var(--ink);
  }
</style>
</head>
<body>
<main class="canvas">
  <article class="business-card">
    <div class="brand-band"></div>
    <div class="brand-dot"></div>
    <h1 class="company-name">KESTON FIELDWORKS</h1>

    <h2 class="person-name">DEAN HARLOW</h2>
    <p class="person-title">DIRECTOR</p>
    <div class="divider"></div>
    <ul class="contact-list">
      <li>0487305526</li>
      <li>dean@kolvat.biz</li>
      <li>www.kestonfieldworks.com</li>
    </ul>
  </article>
</main>
</body>
</html>
```